Website Redesign for Accommodation Directory

We need a redesign for staylistfinderhub.example
The new design needs to include a banner with overlaid text and a 'get started now' button. The overlaid text could be 'Find Hotels in Auckland, New Zealand' for example.
The new design needs to include:
- primary navigation in header
- an accommodation search (left or right column)
- a secondary navigation menu (under the search).
We will need the following font styles (including links for each) defined also please:
h1, h2, h3, h4, h5, h6, p, ul, ol, address, pre
Industry/Entity Type
Accommodation
Look and feel

```html
<!DOCTYPE html>
<html lang="en">
<head>
<meta charset="utf-8">
<title>Stay List Finder Hub</title>
<link href="https://fonts.googleapis.com/css2?family=Arimo:wght@400;700&display=swap" rel="stylesheet">
<style>
:root{
  --red:#c8232b;
  --red-dark:#a51a20;
  --red-soft:#c8434a;
  --text:#555555;
  --muted:#8a8a8a;
  --line:#d8d8d8;
  --panel:#e4e4e4;
  --blue:#1a9ad6;
  --foot-top:#4a4a4a;
  --foot-bottom:#585858;
  --white:#ffffff;
}
*{margin:0;padding:0;box-sizing:border-box}
html,body{width:1029px;height:1200px;overflow:hidden;background:var(--white)}
body{position:relative;font-family:"Arimo",Arial,sans-serif;color:var(--text)}
.abs{position:absolute}
a{color:inherit;text-decoration:none}
ul{list-style:none}

/* header */
.brand{left:103px;top:16px;display:flex;align-items:center;gap:6px}
.brand-mark{width:30px;height:30px;background:var(--red);border-radius:4px}
.brand-name{font-size:29px;font-weight:700;color:#5a5a5a;letter-spacing:-0.5px}
.phone{right:112px;top:29px;display:flex;align-items:center;gap:8px;font-size:14px;font-weight:700;color:#666}

/* primary nav */
.primary-nav{left:102px;top:69px;width:822px;height:48px;background:linear-gradient(#fafafa,#dcdcdc);border-bottom:4px solid var(--red);display:flex;box-shadow:0 2px 3px rgba(0,0,0,.15)}
.primary-nav a{display:flex;align-items:center;justify-content:center;font-size:12.5px;color:#444;border-right:1px solid #c9c9c9;height:44px}
.primary-nav a.is-active{background:var(--red-soft);color:var(--white);height:48px}
.dropdown{left:184px;top:117px;width:204px;height:115px;background:var(--red-soft);z-index:3;display:grid;grid-template-columns:1fr 1fr;padding:10px 8px;box-shadow:0 2px 6px rgba(0,0,0,.3)}
.dropdown ul li{color:var(--white);font-size:9.5px;height:21.5px;display:flex;align-items:center;gap:8px;padding-left:4px}
.dropdown ul:first-child{border-right:1px solid rgba(255,255,255,.6)}
.dropdown ul:last-child{padding-left:10px}
.tri{width:0;height:0;border-left:5px solid currentColor;border-top:4px solid transparent;border-bottom:4px solid transparent}

/* banner */
.banner-shadow{left:40px;top:395px;width:950px;height:30px;background:radial-gradient(ellipse at center,rgba(0,0,0,.25),rgba(0,0,0,0) 70%)}
.banner{left:132px;top:135px;width:762px;height:279px;border:3px solid #555;background:linear-gradient(120deg,#c9a46a 0%,#8a6a48 35%,#cfc3ae 55%,#3a2d24 80%,#1e1a18 100%)}
.banner-caption{left:0;right:0;bottom:0;height:48px;background:rgba(40,40,40,.55);color:var(--white);font-size:12.5px;display:flex;align-items:center;justify-content:flex-end;padding-right:30px}
.slide-btn{width:49px;height:47px;background:var(--red);border-radius:2px;display:flex;align-items:center;justify-content:center;box-shadow:0 2px 3px rgba(0,0,0,.4)}

/* featured */
.featured-bar{left:101px;top:443px;width:823px;height:27px;background:var(--panel);display:flex}
.featured-bar h3{flex:1;font-size:12px;font-weight:700;color:#555;display:flex;align-items:center;justify-content:center}
.thumb{top:480px;width:235px;height:109px;border:3px solid #6a6a6a;box-shadow:0 4px 6px rgba(0,0,0,.25)}
.thumb.pool{left:141px;background:linear-gradient(#1e8ec8,#4cb3e0 60%,#d9d5cc)}
.thumb.indoor{left:394px;background:linear-gradient(#a36b3c,#4aa6b4 70%,#2d7b8a)}
.thumb.lounge{left:648px;background:linear-gradient(#6d4a2d,#d7b98b 55%,#8a5e3a)}
.chev{top:526px}

/* search panel */
.content-box{left:102px;top:616px;width:822px;height:494px;border:1px solid #d4d4d4;border-top:none;background:var(--white)}
.search-bar{left:102px;top:616px;width:822px;height:49px;background:linear-gradient(#f4f4f4,#d9d9d9);border-radius:4px 4px 0 0;border-bottom:1px solid #c4c4c4}
.search-title{left:117px;top:632px;font-size:14px;font-weight:700;color:#555}
.select{top:628px;height:24px;background:var(--white);border:1px solid #cfcfcf;font-size:9px;color:#999;display:flex;align-items:center;justify-content:space-between;padding:0 8px}
.btn-search{left:667px;top:630px;width:58px;height:20px;background:var(--red-soft);border-radius:3px;color:var(--white);font-size:10.5px;display:flex;align-items:center;justify-content:center}
.btn-start{left:761px;top:610px;width:144px;height:35px;background:linear-gradient(#33b3ea,var(--blue));border-radius:3px;color:var(--white);font-size:13px;font-weight:700;display:flex;align-items:center;justify-content:center;gap:8px;box-shadow:0 2px 3px rgba(0,0,0,.3)}

/* left column */
.side h4{font-size:12px;font-weight:700;color:var(--red)}
.sub-nav{display:grid;grid-template-columns:95px 95px;row-gap:0}
.sub-nav li{font-size:10.5px;color:var(--muted);height:26.7px;display:flex;align-items:center;gap:7px}
.sub-nav .tri{border-left-color:#aaa}
.col-rule{left:310px;top:682px;width:2px;height:410px;background:#ccc}
.map{left:125px;top:864px;width:156px;height:101px;background:radial-gradient(ellipse at 40% 40%,#b3b3b3,#d6d6d6 70%,#fff 100%);border-radius:40%}

/* main column */
.welcome-img{left:329px;top:683px;width:188px;height:104px;border:2px solid #cfcfcf;background:linear-gradient(100deg,#5a6a4a,#d9c49a 45%,#6b3a26 80%,#3a2a22)}
.welcome h2{font-size:12px;font-weight:700;color:var(--red)}
.welcome p{font-size:9.6px;line-height:17px;color:#9a9a9a;text-align:justify}
.view-more{right:127px;top:781px;font-size:10.5px;color:var(--red)}
.lead{left:334px;top:810px;width:574px;font-size:15.5px;line-height:24px;color:var(--red-soft)}
.feature{width:260px}
.feature-head{display:flex;align-items:center;gap:8px;height:34px}
.feature-head h3{font-size:13.5px;font-weight:700;color:#444}
.feature p{font-size:8.8px;line-height:14.5px;color:#999;text-align:justify;margin-top:4px}

/* footer */
.footer-links{left:0;top:1110px;width:1029px;height:39px;background:var(--foot-top);display:flex;align-items:center;justify-content:center;gap:8px;font-size:9.5px;color:#eee}
.footer-links span.sep{color:#bbb}
.footer-base{left:0;top:1149px;width:1029px;height:51px;background:var(--foot-bottom);color:#eee;font-size:9px}
.copyright{left:106px;top:20px}
.connect{left:707px;top:14px;display:flex;align-items:center;gap:6px}
.social{width:22px;height:22px;border-radius:50%}
</style>
</head>
<body>

<header>
  <div class="abs brand"><span class="brand-mark"></span><span class="brand-name">staylistfinderhub.example</span></div>
  <div class="abs phone">
    <svg width="18" height="14" viewBox="0 0 18 14"><path d="M1 4 Q9 -2 17 4 L15 6 L12 5 L12 3 Q9 2 6 3 L6 5 L3 6 Z" fill="#c8232b"/><rect x="4" y="7" width="10" height="6" rx="1" fill="#c8232b"/></svg>
    555 010 2748
  </div>
</header>

<nav class="abs primary-nav">
  <a href="#" style="width:82px">Home</a>
  <a href="#" class="is-active" style="width:90px">About Us</a>
  <a href="#" style="width:144px">Add Your Property</a>
  <a href="#" style="width:127px">Supplier Log in</a>
  <a href="#" style="width:168px">Accommodation Search</a>
  <a href="#" style="width:211px;border-right:none;justify-content:flex-start;padding-left:20px">Contact Us</a>
</nav>
<div class="abs dropdown">
  <ul><li><span class="tri"></span>Lorem Ipusem</li><li><span class="tri"></span>Lorem Ipusem</li><li><span class="tri"></span>Lorem Ipusem</li><li><span class="tri"></span>Lorem Ipusem</li></ul>
  <ul><li><span class="tri"></span>Lorem Ipusem</li><li><span class="tri"></span>Lorem Ipusem</li><li><span class="tri"></span>Lorem Ipusem</li><li><span class="tri"></span>Lorem Ipusem</li></ul>
</div>

<div class="abs banner-shadow"></div>
<section class="abs banner" role="img" aria-label="Hotel bedroom photo with beds, seating area and window">
  <div class="abs banner-caption">Find Hotels in Auckland, New Zealand</div>
</section>
<a class="abs slide-btn" style="left:155px;top:247px" href="#"><svg width="14" height="20" viewBox="0 0 14 20"><path d="M11 2 L3 10 L11 18" stroke="#fff" stroke-width="2.5" fill="none"/></svg></a>
<a class="abs slide-btn" style="left:820px;top:247px" href="#"><svg width="14" height="20" viewBox="0 0 14 20"><path d="M3 2 L11 10 L3 18" stroke="#fff" stroke-width="2.5" fill="none"/></svg></a>

<div class="abs featured-bar">
  <h3>Featured Accomodation - 1</h3><h3>Featured Accomodation - 1</h3><h3>Featured Accomodation - 1</h3>
</div>
<svg class="abs chev" style="left:106px" width="18" height="14" viewBox="0 0 18 14"><path d="M9 1 L2 7 L9 13 M16 1 L9 7 L16 13" stroke="#555" stroke-width="3" fill="none"/></svg>
<div class="abs thumb pool" role="img" aria-label="Outdoor pool with striped loungers"></div>
<div class="abs thumb indoor" role="img" aria-label="Indoor resort pool"></div>
<div class="abs thumb lounge" role="img" aria-label="Hotel lounge interior"></div>
<svg class="abs chev" style="left:898px" width="18" height="14" viewBox="0 0 18 14"><path d="M2 1 L9 7 L2 13 M9 1 L16 7 L9 13" stroke="#555" stroke-width="3" fill="none"/></svg>

<div class="abs content-box"></div>
<div class="abs search-bar"></div>
<h2 class="abs search-title">Accommodation Search</h2>
<div class="abs select" style="left:298px;width:170px">All Counries<svg width="10" height="6"><path d="M0 0 L10 0 L5 6Z" fill="#444"/></svg></div>
<div class="abs select" style="left:479px;width:171px">All Categories<svg width="10" height="6"><path d="M0 0 L10 0 L5 6Z" fill="#444"/></svg></div>
<a class="abs btn-search" href="#">Search</a>
<a class="abs btn-start" href="#"><svg width="14" height="14" viewBox="0 0 14 14"><circle cx="7" cy="7" r="7" fill="#fff"/><path d="M5 4 L10 7 L5 10Z" fill="#1a9ad6"/></svg>Get started now</a>

<aside class="side">
  <h4 class="abs" style="left:119px;top:685px">Tertiary navigation</h4>
  <ul class="abs sub-nav" style="left:120px;top:708px">
    <li><span class="tri"></span>Lorem Ipusem</li><li><span class="tri"></span>Lorem Ipusem</li>
    <li><span class="tri"></span>Lorem Ipusem</li><li><span class="tri"></span>Lorem Ipusem</li>
    <li><span class="tri"></span>Lorem Ipusem</li><li><span class="tri"></span>Lorem Ipusem</li>
    <li><span class="tri"></span>Lorem Ipusem</li><li><span class="tri"></span>Lorem Ipusem</li>
  </ul>
  <h4 class="abs" style="left:119px;top:835px">Locate&nbsp; Your Accommodation</h4>
  <div class="abs map" role="img" aria-label="World map for locating accommodation"></div>
  <ul class="abs sub-nav" style="left:116px;top:971px">
    <li><span class="tri"></span>Lorem Ipusem</li><li><span class="tri"></span>Lorem Ipusem</li>
    <li><span class="tri"></span>Lorem Ipusem</li><li><span class="tri"></span>Lorem Ipusem</li>
    <li><span class="tri"></span>Lorem Ipusem</li><li><span class="tri"></span>Lorem Ipusem</li>
    <li><span class="tri"></span>Lorem Ipusem</li><li><span class="tri"></span>Lorem Ipusem</li>
  </ul>
</aside>
<div class="abs col-rule"></div>

<main>
  <div class="abs welcome-img" role="img" aria-label="Bright hotel bedroom with tall windows"></div>
  <div class="abs welcome" style="left:531px;top:683px;width:375px">
    <h2>Welcome To Our SIte</h2>
    <p style="margin-top:8px">It is a long established fact that a reader will be distracted by the readable content of a page when looking at its layout. The point of using Lorem Ipsum is that it has a more-or-less normal distribution of letters, as opposed to using 'Content here, content here', making it look like readable English.</p>
  </div>
  <a class="abs view-more" href="#">View more</a>
  <p class="abs lead">You’ve come to the right place to find Accommodation in Any Country whether it’s a hotel, motel, backpackers, bed and breakfast or beach house you're after you'll find just what you need to enjoy your stay in Any Country.</p>

  <div class="abs feature" style="left:346px;top:900px">
    <div class="feature-head"><svg width="36" height="30" viewBox="0 0 36 30"><path d="M3 10 Q18 0 33 10 L30 14 L25 12 L25 9 Q18 7 11 9 L11 12 L6 14Z" fill="#333"/><rect x="8" y="15" width="20" height="12" rx="3" fill="#444"/><circle cx="18" cy="21" r="4" fill="#888"/></svg><h3>Contact Us</h3></div>
    <p>Cicero are also reproduced in their exact original form, accompanied by English versions from the 1914 translation by H. Rackham.</p>
  </div>
  <div class="abs feature" style="left:640px;top:900px">
    <div class="feature-head"><svg width="28" height="30" viewBox="0 0 28 30"><circle cx="14" cy="9" r="7" fill="#e0a060"/><path d="M2 30 Q2 17 14 17 Q26 17 26 30Z" fill="#8a8a8a"/></svg><h3 style="margin-left:6px">Guides</h3></div>
    <p>Cicero are also reproduced in their exact original form, accompanied by English versions from the 1914 translation by H. Rackham.</p>
  </div>
  <div class="abs feature" style="left:346px;top:995px">
    <div class="feature-head"><svg width="32" height="30" viewBox="0 0 32 30"><path d="M16 1 L31 28 L1 28Z" fill="#f39a1e"/><rect x="14.5" y="10" width="3" height="10" fill="#fff"/><rect x="14.5" y="22" width="3" height="3" fill="#fff"/></svg><h3 style="margin-left:6px">Get Instant Alerts</h3></div>
    <p>Cicero are also reproduced in their exact original form, accompanied by English versions from the 1914 translation by H. Rackham.</p>
  </div>
  <div class="abs feature" style="left:638px;top:995px">
    <div class="feature-head"><svg width="32" height="32" viewBox="0 0 32 32"><circle cx="16" cy="16" r="15" fill="#2f6fd0"/><path d="M11 12 Q11 7 16 7 Q21 7 21 12 Q21 15 17 17 L17 20" stroke="#fff" stroke-width="3" fill="none"/><circle cx="17" cy="25" r="2" fill="#fff"/></svg><h3 style="margin-left:6px">FAQ’s</h3></div>
    <p>Cicero are also reproduced in their exact original form, accompanied by English versions from the 1914 translation by H. Rackham.</p>
  </div>
</main>

<footer>
  <nav class="abs footer-links">
    <a href="#">Home</a><span class="sep">|</span><a href="#">About Us</a><span class="sep">|</span><a href="#">Add Your Property</a><span class="sep">|</span><a href="#">Supplier Log in</a><span class="sep">|</span><a href="#">Accommodation Search</a><span class="sep">|</span><a href="#">Contact Us</a><span class="sep">|</span><a href="#">FAQ</a><span class="sep">|</span><a href="#">Sitemap</a>
  </nav>
  <div class="abs footer-base">
    <address class="abs copyright" style="font-style:normal">Copyright © 2011 staylistfinderhub.example&nbsp;&nbsp; All rights reserved</address>
    <div class="abs connect">Connect with us:
      <span class="social" style="background:#4a67a8;margin-left:6px"></span>
      <span class="social" style="background:#3ab0e2"></span>
      <span class="social" style="background:#f08a1c"></span>
      <span class="social" style="background:#3a3a3a"></span>
      <span class="social" style="background:#6a2a9a"></span>
    </div>
  </div>
</footer>

</body>
</html>
```